Music Studio and Store Business Card and Logo Design

We need a business card and logo design for an existing Music Studio (Piano and Voice) which will soon expand to offer retail sheet music for all instruments including voice. The expanding store will not sell or lease instruments. We are a well known Fine Arts Studio for instruction to children, college students, and adults with 42 enrolled students and a wait list. We want something with simple elegance, but not archaic. Even a sleek modern look is okay. We do not want something childish or too fun looking because we do serve ages 5 - 62. We would also like the logo workable/transferable to signage for our new location opening in March. We like classic burgundy, black, deep blues, but are open to other suggestions. We included our studio brochure so you can get to know us a little better and some images we thought were interesting with the use of clef signs for the & and using note heads for the bottom or top of the letter "H"

Target Market(s)

All ages

Industry/Entity Type

Business

Contact Information for Business Card

H&H Music StudioPlattsburgh, NYWanda J. Haby and Oren M. Castaldi, Owners

Requirements
Must have
• Phone Number: (555) 817-4062
• Website: www.rbtonalartsroom.example
Nice to have
• Email: lorna@rbtonalartsroom.example
Should not have
• Any instruments on the card other than piano. Instrument pix is not a necessity.

```html
<!DOCTYPE html>
<html lang="en">
<head>
<meta charset="utf-8">
<title>R&amp;B Music Studio – Business Cards</title>
<link rel="stylesheet" href="https://fonts.googleapis.com/css2?family=Josefin+Sans:wght@300&family=Open+Sans:wght@400;700&display=swap">
<style>
  :root {
    --backdrop: #3a3430;
    --card: #0e0e0e;
    --card-edge: #1c1c1c;
    --ink-white: #f2f2f2;
    --ink-soft: #bdbdbd;
    --ink-silver: #b9b9b9;
    --divider: #2c2c2c;
  }
  * { margin: 0; padding: 0; box-sizing: border-box; }
  html, body {
    width: 1200px;
    height: 900px;
    overflow: hidden;
    background: var(--backdrop);
  }
  .canvas {
    position: relative;
    width: 1200px;
    height: 900px;
    display: flex;
    align-items: center;
    justify-content: center;
    gap: 60px;
  }
  .card {
    position: relative;
    width: 525px;
    height: 300px;
    background: var(--card);
    border: 1px solid var(--card-edge);
    box-shadow: 0 10px 30px rgba(0,0,0,0.45);
  }
  .brand-name {
    font-family: "Josefin Sans", sans-serif;
    font-weight: 300;
    line-height: 1.15;
    letter-spacing: 0.02em;
  }

  /* Contact side */
  .card--contact .brand-name {
    position: absolute;
    left: 42px;
    top: 130px;
    font-size: 34px;
    color: var(--ink-white);
  }
  .card--contact .divider {
    position: absolute;
    left: 305px;
    top: 40px;
    width: 1px;
    height: 220px;
    background: var(--divider);
  }
  .contact-block {
    position: absolute;
    left: 326px;
    top: 52px;
    width: 190px;
    font-family: "Open Sans", sans-serif;
    color: var(--ink-white);
  }
  .owner-name {
    font-size: 14px;
    font-weight: 700;
    line-height: 1.45;
  }
  .owner-role {
    margin-top: 4px;
    font-size: 11px;
    color: var(--ink-soft);
  }
  .location {
    margin-top: 20px;
    font-size: 11px;
    color: var(--ink-soft);
  }
  .contact-details {
    margin-top: 14px;
    list-style: none;
    font-size: 11px;
    line-height: 1.7;
    color: var(--ink-soft);
    white-space: nowrap;
  }

  /* Logo side */
  .card--logo {
    display: flex;
    align-items: center;
    justify-content: center;
  }
  .card--logo .brand-name {
    font-size: 44px;
    text-align: center;
    color: var(--ink-silver);
  }
</style>
</head>
<body>
  <main class="canvas">
    <section class="card card--contact">
      <p class="brand-name">R&amp;B<br>Music Studio</p>
      <div class="divider"></div>
      <div class="contact-block">
        <p class="owner-name">Lorna P. Quist</p>
        <p class="owner-name">Oren M. Castaldi</p>
        <p class="owner-role">Owners</p>
        <p class="location">Harrowfield, NY</p>
        <ul class="contact-details">
          <li class="phone">(555) 817-4062</li>
          <li class="website">www.rbtonalartsroom.example</li>
          <li class="email">lorna@rbtonalartsroom.example</li>
        </ul>
      </div>
    </section>

    <section class="card card--logo">
      <p class="brand-name">R&amp;B<br>Music Studio</p>
    </section>
  </main>
</body>
</html>
```